Gooey Tides

I am creating an online slime shop that will sell handmade custom slimes. I need to be able to have payment/shipping options and the ability to change product photos since the product and product name will change often

Target Market(s)

Slime

Industry/Entity Type

Retail - online sales

Coding

Coded - Design and coding required

Number of Pages Required

2 page

Font styles to use
Sans Serif

Colors
0094D4
00A9DD
6FCCEA
C7EBF8
E9F6FB
E54698
E96AAD
F1A4CE
F9D9EA
FCEFF6
A7469A
B969AE
D3A5CF
EDDBEB
F8F0F9

Requirements
Must have
• My logo, my domain, ability to change photos of products for sale, payment options, shipping options, social media links, contact us,

```html
<!DOCTYPE html>
<html lang="en">
<head>
<meta charset="utf-8">
<title>Gooey Tides — Handmade Slime Shop</title>
<link href="https://fonts.googleapis.com/css2?family=Poppins:wght@500;600;700;800&family=Roboto:ital,wght@0,400;0,500;0,700;1,400&display=swap" rel="stylesheet">
<style>
:root{
  --blue-deep:#0094D4;
  --blue:#00A9DD;
  --blue-mid:#6FCCEA;
  --blue-light:#C7EBF8;
  --blue-pale:#E9F6FB;
  --pink:#E54698;
  --pink-mid:#E96AAD;
  --pink-soft:#F1A4CE;
  --pink-light:#F9D9EA;
  --pink-pale:#FCEFF6;
  --purple:#A7469A;
  --purple-mid:#B969AE;
  --purple-soft:#D3A5CF;
  --purple-light:#EDDBEB;
  --purple-pale:#F8F0F9;
  --violet:#8f2fc4;
  --header-bg:#9fdfdd;
  --text:#222;
  --muted:#666;
  --star:#f7a21b;
}
*{box-sizing:border-box;margin:0;padding:0}
html,body{width:1200px;height:3683px;overflow:hidden}
body{font-family:'Roboto',sans-serif;color:var(--text);background:#fff;position:relative}
a{color:inherit;text-decoration:none}

/* top bar */
.promo-bar{position:absolute;top:0;left:0;width:1200px;height:31px;background:var(--pink);color:#fff;font-size:13px;display:flex;align-items:center;justify-content:space-between;padding:0 80px 0 142px}

/* header */
.site-header{position:absolute;top:31px;left:0;width:1200px;height:80px;background:var(--header-bg)}
.brand{position:absolute;left:142px;top:22px;display:flex;align-items:center;gap:10px;font-family:'Poppins',sans-serif;font-weight:700;font-size:22px;color:var(--purple)}
.brand-dot{width:34px;height:34px;border-radius:50%;background:#fff}
.search{position:absolute;left:338px;top:24px;width:333px;height:34px;background:#fff;border-radius:3px;font-size:13px;color:#888;padding:9px 20px}
.search-btn{position:absolute;right:5px;top:4px;width:26px;height:26px;border-radius:3px;background:var(--violet);display:flex;align-items:center;justify-content:center}
.header-links{position:absolute;left:684px;top:10px;display:flex}
.header-link{width:137px;height:58px;display:flex;flex-direction:column;align-items:center;justify-content:center;gap:6px;font-size:13px;color:#333;border-left:1px solid #bfe6e6}
.header-link:first-child{border-left:none}

/* nav */
.main-nav{position:absolute;top:111px;left:0;width:1200px;height:48px;background:#fff;display:flex;padding-left:110px;font-size:13px;font-weight:500;color:#222}
.main-nav a{height:48px;display:flex;align-items:center;padding:0 14px}
.main-nav a.active{background:linear-gradient(180deg,var(--purple-mid),var(--violet));color:#fff;position:relative}
.main-nav a.active::after{content:"";position:absolute;left:50%;bottom:-8px;margin-left:-8px;border:8px solid transparent;border-bottom:0;border-top-color:#fff}

/* hero */
.hero{position:absolute;top:159px;left:0;width:1200px;height:480px;background:linear-gradient(180deg,#3fa4e4 0%,#62b7ec 45%,#b8d6f3 78%,#f4e4f4 100%);overflow:hidden}
.hero-art{position:absolute;left:0;top:0;width:640px;height:480px;background:linear-gradient(180deg,#52b0e8 0%,#7cc2ee 55%,#e9c4e6 100%)}
.hero-copy{position:absolute;left:684px;top:110px;width:380px}
.hero-title{font-family:'Poppins',sans-serif;font-weight:800;font-size:45px;color:var(--pink);letter-spacing:.5px;line-height:1}
.hero-text{font-size:15.5px;line-height:24px;color:#1d2a3a;margin-top:18px}
.btn-solid{display:inline-flex;align-items:center;justify-content:center;background:linear-gradient(180deg,var(--purple-mid),var(--violet));color:#fff;font-weight:700;font-size:14px;border-radius:3px}
.hero .btn-solid{margin-top:18px;width:126px;height:41px}
.circle-btn{position:absolute;width:42px;height:42px;border-radius:50%;background:#fff;display:flex;align-items:center;justify-content:center;box-shadow:0 1px 3px rgba(0,0,0,.12)}

/* section heads */
.section-head{position:absolute;left:0;width:1200px;text-align:center}
.eyebrow{font-size:15px;font-weight:700;letter-spacing:.3px;color:#111}
.section-title{font-family:'Poppins',sans-serif;font-weight:800;font-size:40px;line-height:48px;background:linear-gradient(90deg,var(--violet),var(--pink));-webkit-background-clip:text;background-clip:text;color:transparent}
.section-title.brand-title{background:none;color:var(--purple)}
.section-lead{font-size:15.5px;line-height:24px;color:#333;width:540px;margin:6px auto 0}

/* category cards */
.cat-card{position:absolute;top:844px;width:289px;height:413px;border:1px solid #bbb;background:#fff;text-align:center}
.cat-photo{height:199px;position:relative;overflow:hidden}
.ribbon{position:absolute;left:-34px;top:26px;width:140px;transform:rotate(-45deg);background:var(--blue);color:#fff;font-size:10px;font-weight:700;padding:4px 0;text-align:center;letter-spacing:.3px}
.cat-name{font-size:20px;font-weight:500;margin-top:22px}
.cat-text{font-size:13.5px;line-height:22px;color:#666;width:240px;margin:10px auto 0}
.btn-outline{display:inline-flex;align-items:center;justify-content:center;border:2px solid var(--pink);color:var(--pink);font-weight:500;font-size:14px;border-radius:3px;background:#fff}
.cat-card .btn-outline,.cat-card .btn-solid{margin-top:16px;width:170px;height:44px}

/* divider band */
.cloud-band{position:absolute;left:0;top:1258px;width:1200px;height:260px;background:linear-gradient(180deg,#fff 0%,#b9dcf2 40%,#ececee 70%,#fff 100%)}

/* products */
.product{position:absolute;top:1687px;width:212px;text-align:center}
.product-photo{height:182px;border:2px solid #ddd;border-radius:6px;overflow:hidden;padding:4px}
.product-photo.selected{border-color:var(--pink)}
.product-fill{width:100%;height:100%;border-radius:3px}
.product-name{font-size:15px;font-weight:700;margin-top:16px}
.product-price{font-size:24px;margin-top:12px;color:#111}
.product .btn-outline{margin-top:14px;width:170px;height:43px;font-size:14px}

/* why */
.why{position:absolute;top:2062px;left:0;width:1200px;height:569px;background:linear-gradient(180deg,#fff 0%,var(--blue-pale) 30%,#f3f9fd 100%)}
.why-card{position:absolute;top:2277px;width:289px;height:256px;background:#fff;border:2px solid var(--pink-pale);border-radius:6px;box-shadow:0 4px 14px rgba(229,70,152,.08);text-align:center}
.why-icon{margin:30px auto 0;width:70px;height:70px;display:block}
.why-name{font-size:20px;font-weight:500;margin-top:12px}
.why-text{font-size:13.5px;line-height:22px;color:#666;width:250px;margin:14px auto 0}

/* testimonials */
.reviews{position:absolute;top:2631px;left:0;width:1200px;height:579px;background:#f3f9fd}
.review-card{position:absolute;top:2823px;width:441px;height:282px;background:#fff;border:2px solid var(--pink-light);border-radius:6px;padding:30px 42px;overflow:hidden}
.stars{color:var(--star);font-size:18px;letter-spacing:4px}
.review-text{font-style:italic;font-size:14.5px;line-height:24px;color:#555;margin-top:12px;position:relative;z-index:1}
.reviewer{display:flex;align-items:center;gap:16px;margin-top:18px;position:relative;z-index:1}
.avatar{width:70px;height:70px;border-radius:50%;background:linear-gradient(180deg,#c7a48a,#7d6a5e);border:3px solid var(--blue-mid)}
.reviewer-name{font-size:19px;font-weight:500}
.reviewer-co{font-size:14px;color:#666;margin-top:4px}
.quote-mark{position:absolute;right:40px;bottom:-70px;font-family:'Poppins',sans-serif;font-size:190px;font-weight:700;color:#eee;line-height:1}

/* footer */
.site-footer{position:absolute;top:3210px;left:0;width:1200px;height:473px;background:var(--blue-deep);color:#fff}
.foot-brand{position:absolute;left:110px;top:110px;display:flex;align-items:center;gap:10px;font-family:'Poppins',sans-serif;font-weight:700;font-size:26px;color:#fff}
.foot-brand .brand-dot{width:40px;height:40px;background:#fff}
.socials{position:absolute;left:150px;top:234px;display:flex;gap:28px}
.socials span{width:18px;height:18px;border-radius:50%;background:#fff;opacity:.9}
.foot-col{position:absolute;top:88px}
.foot-col h4{font-size:19px;font-weight:700;margin-bottom:14px}
.foot-col a{display:block;font-size:15px;line-height:32px}
.foot-col p{font-size:15px;line-height:32px}
.email-input{width:286px;height:49px;background:#fff;border-radius:3px;color:#333;font-size:15px;padding:15px 26px;margin-top:10px}
.foot-col .btn-solid{display:flex;margin-top:8px;width:109px;height:46px;line-height:1;font-size:15px;background:linear-gradient(180deg,var(--pink-mid),var(--violet))}
.contact-item{position:absolute;top:308px;display:flex;gap:14px;align-items:center;font-size:15px;line-height:24px}
.contact-icon{width:40px;height:40px;border-radius:50%;background:#1a7dc2;display:flex;align-items:center;justify-content:center}
.copyright{position:absolute;top:398px;left:0;width:1200px;text-align:center;font-size:15px}
.pay-cards{position:absolute;top:431px;left:514px;display:flex;gap:4px}
.pay-cards span{width:26px;height:16px;border-radius:2px;background:#fff}
</style>
</head>
<body>

<div class="promo-bar">
  <span>Use Code GOOEY10 to get 10% OFF</span>
  <span>Processing Time: 3-5 Business Days</span>
  <span>FREE Shipping $97+ (USA only)</span>
</div>

<header class="site-header">
  <a class="brand" href="#"><span class="brand-dot"></span>Gooey Tides</a>
  <div class="search">Search products
    <span class="search-btn"><svg width="12" height="12" viewBox="0 0 12 12"><circle cx="5" cy="5" r="3.6" fill="none" stroke="#fff" stroke-width="1.6"/><path d="M7.6 7.6L11 11" stroke="#fff" stroke-width="1.6"/></svg></span>
  </div>
  <nav class="header-links">
    <a class="header-link" href="#"><svg width="11" height="11" viewBox="0 0 12 12"><circle cx="6" cy="3.5" r="3" fill="#222"/><path d="M0.5 12a5.5 4.5 0 0 1 11 0z" fill="#222"/></svg>My Account</a>
    <a class="header-link" href="#"><svg width="12" height="11" viewBox="0 0 12 11"><rect x="0.5" y="0.5" width="6" height="10" fill="none" stroke="#222"/><path d="M4 5.5h7M8.5 3l2.5 2.5L8.5 8" fill="none" stroke="#222" stroke-width="1.3"/></svg>Checkout</a>
    <a class="header-link" href="#"><svg width="13" height="11" viewBox="0 0 13 11"><path d="M0 1h2.5l1.8 6h6.5l1.5-4.5H3.4" fill="none" stroke="#222" stroke-width="1.4"/><circle cx="5" cy="9.5" r="1.2" fill="#222"/><circle cx="10" cy="9.5" r="1.2" fill="#222"/></svg>My Cart</a>
  </nav>
</header>

<nav class="main-nav">
  <a class="active" href="#">HOME</a>
  <a href="#">SLIME SHOP</a>
  <a href="#">CUSTOM SLIME</a>
  <a href="#">AROMATHERAPY SLIME</a>
  <a href="#">SLIME SUPPLIES</a>
  <a href="#">SLIME CARE</a>
  <a href="#">FAQ</a>
  <a href="#">BLOG</a>
  <a href="#">ABOUT</a>
  <a href="#">CONTACT</a>
</nav>

<section class="hero">
  <div class="hero-art" role="img" aria-label="Hero scene: blue pond-themed slime on a pink pedestal beside a sleepy bear on a moon and pastel clouds"></div>
  <div class="hero-copy">
    <h1 class="hero-title">GOOEY TIDES</h1>
    <p class="hero-text">Lorem ipsum dolor sit amet, consectetur adipiscing elit, sed do eiusmod tempor incididunt ut labore et dolore magna aliqua.</p>
    <a class="btn-solid" href="#">SHOP SLIMES</a>
  </div>
  <a class="circle-btn" style="left:686px;top:392px" href="#"><svg width="10" height="14" viewBox="0 0 10 14"><path d="M8 1L2 7l6 6" fill="none" stroke="#222" stroke-width="2"/></svg></a>
  <a class="circle-btn" style="left:736px;top:392px" href="#"><svg width="10" height="14" viewBox="0 0 10 14"><path d="M2 1l6 6-6 6" fill="none" stroke="#222" stroke-width="2"/></svg></a>
</section>

<div class="section-head" style="top:709px">
  <p class="eyebrow">WELCOME TO</p>
  <h2 class="section-title brand-title">GOOEY TIDES</h2>
  <p class="section-lead">Lorem ipsum dolor sit amet, consectetur adipiscing elit, sed do eiusmod tempor incididunt ut labore et dolore magna aliqua.</p>
</div>

<article class="cat-card" style="left:143px">
  <div class="cat-photo" role="img" aria-label="Photo of a jar of pink and yellow custom slime with squishy toppers" style="background:linear-gradient(180deg,#f48fb1,#f3d79a)"><span class="ribbon">BEST SELLER</span></div>
  <h3 class="cat-name">My Custom Slime</h3>
  <p class="cat-text">Lorem ipsum dolor sit amet, cons ectetur adipiscing elit, sed do et dolore magna aliqua.</p>
  <a class="btn-outline" href="#">CREATE MY SLIME</a>
</article>
<article class="cat-card" style="left:455px">
  <div class="cat-photo" role="img" aria-label="Photo of pink waffle-textured aromatherapy slime with sprinkles" style="background:linear-gradient(180deg,#e6b5b8,#d88bb6)"><span class="ribbon">BEST SELLER</span></div>
  <h3 class="cat-name">Aromatherapy Slime</h3>
  <p class="cat-text">Lorem ipsum dolor sit amet, cons ectetur adipiscing elit, sed do et dolore magna aliqua.</p>
  <a class="btn-solid" href="#">VIEW COLLECTION</a>
</article>
<article class="cat-card" style="left:767px">
  <div class="cat-photo" role="img" aria-label="Photo of green slime supplies scene with a tiny tree and figurines" style="background:linear-gradient(180deg,#7f8a86,#6fcf9e)"><span class="ribbon">BEST SELLER</span></div>
  <h3 class="cat-name">Slime Supplies</h3>
  <p class="cat-text">Lorem ipsum dolor sit amet, cons ectetur adipiscing elit, sed do et dolore magna aliqua.</p>
  <a class="btn-outline" href="#">CHOOSE SUPPLIES</a>
</article>

<div class="cloud-band" role="img" aria-label="Decorative band of white cartoon clouds"></div>

<div class="section-head" style="top:1566px">
  <h2 class="section-title">NEW SLIME RELEASES</h2>
  <p class="section-lead">Lorem ipsum dolor sit amet, consectetur adipiscing elit, sed do eiusmod tempor incididunt ut labore et dolore magna aliqua.</p>
</div>

<a class="circle-btn" style="left:51px;top:1766px;border:1px solid #999;box-shadow:none" href="#"><svg width="10" height="14" viewBox="0 0 10 14"><path d="M8 1L2 7l6 6" fill="none" stroke="#222" stroke-width="1.6"/></svg></a>
<a class="circle-btn" style="left:1107px;top:1766px;border:1px solid #999;box-shadow:none" href="#"><svg width="10" height="14" viewBox="0 0 10 14"><path d="M2 1l6 6-6 6" fill="none" stroke="#222" stroke-width="1.6"/></svg></a>

<div class="product" style="left:144px">
  <div class="product-photo"><div class="product-fill" role="img" aria-label="Photo of light blue pond slime" style="background:linear-gradient(180deg,#7fd3f0,#2ba9d6)"></div></div>
  <p class="product-name">Lorem ipsum dolor sit</p><p class="product-price">$30.00</p>
</div>
<div class="product" style="left:377px">
  <div class="product-photo selected"><div class="product-fill" role="img" aria-label="Photo of deep teal ocean slime with glitter" style="background:linear-gradient(180deg,#3a9bbd,#0d6688)"></div></div>
  <p class="product-name">Lorem ipsum dolor sit</p><p class="product-price">$30.00</p>
  <a class="btn-outline" href="#">ADD TO CART</a>
</div>
<div class="product" style="left:610px">
  <div class="product-photo"><div class="product-fill" role="img" aria-label="Photo of red-orange slime with purple toppings" style="background:linear-gradient(180deg,#f27a5a,#d23c22)"></div></div>
  <p class="product-name">Lorem ipsum dolor sit</p><p class="product-price">$30.00</p>
</div>
<div class="product" style="left:843px">
  <div class="product-photo"><div class="product-fill" role="img" aria-label="Photo of emerald green glitter slime" style="background:linear-gradient(180deg,#3bb57a,#0e7445)"></div></div>
  <p class="product-name">Lorem ipsum dolor sit</p><p class="product-price">$30.00</p>
</div>

<section class="why"></section>
<div class="section-head" style="top:2151px">
  <h2 class="section-title">WHY GOOEY TIDES?</h2>
  <p class="section-lead">Lorem ipsum dolor sit amet, consectetur adipiscing elit, sed do eiusmod tempor incididunt ut labore et dolore magna aliqua.</p>
</div>

<article class="why-card" style="left:143px">
  <svg class="why-icon" viewBox="0 0 70 70"><circle cx="42" cy="30" r="22" fill="var(--pink-pale)"/><path d="M12 30h20c6 0 6 8 0 8H22M12 42h26c6 0 8-6 4-9M18 22c10-6 24-6 30 4" fill="none" stroke="var(--purple)" stroke-width="2.4" stroke-linecap="round"/></svg>
  <h3 class="why-name">Amazing Slimes</h3>
  <p class="why-text">Lorem ipsum dolor sit amet, cons ectetur adipiscing elit, sed do et dolore magna aliqua.</p>
</article>
<article class="why-card" style="left:455px">
  <svg class="why-icon" viewBox="0 0 70 70"><rect x="32" y="6" width="26" height="58" fill="var(--pink-pale)" stroke="var(--purple)" stroke-width="2.4"/><rect x="12" y="34" width="26" height="22" fill="#fff" stroke="var(--purple)" stroke-width="2.4"/><path d="M12 42h26M38 12h14" stroke="var(--purple)" stroke-width="2.4"/></svg>
  <h3 class="why-name">Stunning Packaging</h3>
  <p class="why-text">Lorem ipsum dolor sit amet, cons ectetur adipiscing elit, sed do et dolore magna aliqua.</p>
</article>
<article class="why-card" style="left:767px">
  <svg class="why-icon" viewBox="0 0 70 70"><path d="M35 4l24 9v18c0 16-10 28-24 34C21 59 11 47 11 31V13z" fill="var(--pink-pale)" stroke="var(--purple)" stroke-width="2.4"/><rect x="26" y="32" width="18" height="14" rx="2" fill="none" stroke="var(--purple)" stroke-width="2.4"/><path d="M29 32v-5a6 6 0 0 1 12 0v5" fill="none" stroke="var(--purple)" stroke-width="2.4"/></svg>
  <h3 class="why-name">Secure Checkout</h3>
  <p class="why-text">Lorem ipsum dolor sit amet, cons ectetur adipiscing elit, sed do et dolore magna aliqua.</p>
</article>

<section class="reviews"></section>
<div class="section-head" style="top:2702px">
  <h2 class="section-title">WHAT OUR CUSTOMERS SAY</h2>
  <p class="section-lead">Lorem ipsum dolor sit amet, consectetur adipiscing elit, sed do eiusmod tempor incididunt ut labore et dolore magna aliqua.</p>
</div>

<a class="circle-btn" style="left:51px;top:2942px;border:1px solid #999;box-shadow:none" href="#"><svg width="10" height="14" viewBox="0 0 10 14"><path d="M8 1L2 7l6 6" fill="none" stroke="#222" stroke-width="1.6"/></svg></a>
<a class="circle-btn" style="left:1107px;top:2942px;border:1px solid #999;box-shadow:none" href="#"><svg width="10" height="14" viewBox="0 0 10 14"><path d="M2 1l6 6-6 6" fill="none" stroke="#222" stroke-width="1.6"/></svg></a>

<article class="review-card" style="left:143px">
  <div class="stars">★★★★★</div>
  <p class="review-text">“Lorem ipsum dolor sit amet, consectetur adipiscing elit, sed do eiusmod tempor incididunt ut labore et dolore magna aliqua. Ut enim ad minim veniam, quis nostrud exercitation ullamco laboris nisi ut aliquip ex fugiat nulla pariatur.”</p>
  <div class="reviewer"><div class="avatar" role="img" aria-label="Customer portrait photo"></div><div><p class="reviewer-name">Sam Rivers</p><p class="reviewer-co">Company name</p></div></div>
  <span class="quote-mark">“</span>
</article>
<article class="review-card" style="left:616px">
  <div class="stars">★★★★★</div>
  <p class="review-text">“Lorem ipsum dolor sit amet, consectetur adipiscing elit, sed do eiusmod tempor incididunt ut labore et dolore magna aliqua. Ut enim ad minim veniam, quis nostrud exercitation ullamco laboris nisi ut aliquip ex fugiat nulla pariatur.”</p>
  <div class="reviewer"><div class="avatar" role="img" aria-label="Customer portrait photo"></div><div><p class="reviewer-name">Sam Rivers</p><p class="reviewer-co">Company name</p></div></div>
  <span class="quote-mark">“</span>
</article>

<footer class="site-footer">
  <div class="foot-brand"><span class="brand-dot"></span>Gooey Tides</div>
  <div class="socials"><span></span><span></span><span></span></div>

  <div class="foot-col" style="left:387px"><h4>CUSTOMER CARE</h4><a href="#">My Account</a><a href="#">Order Tracking</a><a href="#">Slime Care</a><a href="#">FAQ</a></div>
  <div class="foot-col" style="left:595px"><h4>POLICIES</h4><a href="#">Terms and Conditions</a><a href="#">Privacy Policy</a><a href="#">About Us</a><a href="#">Contact Us</a></div>
  <div class="foot-col" style="left:809px"><h4>JOIN US</h4><p>Join the Gooey Tides family!</p><div class="email-input">Email address</div><a class="btn-solid" href="#">SIGN UP!</a></div>

  <div class="contact-item" style="left:143px"><span class="contact-icon"><svg width="12" height="16" viewBox="0 0 12 16"><path d="M6 0a6 6 0 0 0-6 6c0 4.5 6 10 6 10s6-5.5 6-10a6 6 0 0 0-6-6z" fill="#fff"/><circle cx="6" cy="6" r="2.2" fill="#1a7dc2"/></svg></span><div>Address :<br>123, Lorem ipsum dolor sit</div></div>
  <div class="contact-item" style="left:479px"><span class="contact-icon"><svg width="14" height="14" viewBox="0 0 14 14"><path d="M3 0.5l2.5 3-1.5 2c1 2 2.5 3.5 4.5 4.5l2-1.5 3 2.5-1.5 2.5C6 13.5 0.5 8 0.5 2z" fill="#fff"/></svg></span><div>Phone :<br>+1 555 014 2290</div></div>
  <div class="contact-item" style="left:814px"><span class="contact-icon"><svg width="16" height="12" viewBox="0 0 16 12"><rect width="16" height="12" rx="1.5" fill="#fff"/><path d="M1 1.5l7 5 7-5" fill="none" stroke="#1a7dc2" stroke-width="1.4"/></svg></span><div>Email :<br>hello@gooeytides.shop</div></div>

  <p class="copyright">© Copyrights 2024 | All Rights Reserved</p>
  <div class="pay-cards"><span></span><span></span><span></span><span></span><span></span><span></span></div>
</footer>

</body>
</html>
```